Business card for medical clinic

I need an upmarket, modern medical/health business card for my clinic

Contact Information for Business Card

name, address, email, qr code

```html
<!DOCTYPE html>
<html lang="en">
<head>
<meta charset="utf-8">
<title>Larkwell Health Partners – Business Card</title>
<link href="https://fonts.googleapis.com/css2?family=Montserrat:wght@400;500;600&display=swap" rel="stylesheet">
<style>
  :root {
    --page-bg: #1f2b38;
    --card-white: #ffffff;
    --navy: #1d3f63;
    --deep-blue: #1c4a72;
    --sky: #2a9fd6;
    --band-dark-start: #1e3f66;
    --band-dark-end: #1f6e9c;
    --band-light-start: #1e5d8c;
    --band-light-end: #2aa0d6;
    --ink: #222831;
  }
  * { box-sizing: border-box; margin: 0; padding: 0; }
  html, body {
    width: 1200px; height: 900px; overflow: hidden;
    background: var(--page-bg);
    font-family: "Montserrat", sans-serif;
  }
  .stage { position: relative; width: 1200px; height: 900px; }

  .card {
    position: absolute;
    border-radius: 18px;
    overflow: hidden;
    box-shadow: 0 10px 24px rgba(0,0,0,.35);
  }

  /* Front */
  .card-front {
    left: 286px; top: 57px; width: 600px; height: 361px;
    background: var(--card-white);
  }
  .brand {
    position: absolute; left: 24px; top: 56px;
    display: flex; align-items: center; gap: 14px;
  }
  .brand-dot {
    width: 40px; height: 40px; border-radius: 50%;
    background: var(--sky);
  }
  .brand-name {
    font-weight: 600; font-size: 25px; color: var(--navy);
    letter-spacing: .5px;
  }
  .person { position: absolute; left: 24px; top: 252px; }
  .person-name { font-weight: 600; font-size: 24px; color: var(--sky); line-height: 1.1; }
  .person-role { font-weight: 400; font-size: 14px; color: var(--ink); margin-top: 2px; }

  .bands { position: absolute; left: 0; top: 0; }
  .contact {
    position: absolute; display: flex; align-items: center; gap: 12px;
    font-size: 14.5px; font-weight: 400;
  }
  .contact svg { flex: none; }
  .contact-phone { left: 364px; top: 280px; color: #fff; font-size: 16px; gap: 20px; }
  .contact-email { left: 24px; top: 329px; color: #fff; }
  .contact-web { left: 334px; top: 329px; color: var(--ink); }

  /* Back */
  .card-back {
    left: 282px; top: 470px; width: 608px; height: 366px;
    background: linear-gradient(135deg, #22375a 0%, #23628f 50%, #2599d0 100%);
    display: flex; align-items: center; justify-content: center; gap: 18px;
  }
  .card-back .brand-dot { width: 54px; height: 54px; background: #ffffff; }
  .card-back .brand-name { color: #ffffff; font-size: 30px; }
</style>
</head>
<body>
<main class="stage">

  <section class="card card-front" aria-label="Business card front">
    <div class="brand">
      <span class="brand-dot"></span>
      <span class="brand-name">Larkwell Health Partners</span>
    </div>

    <svg class="bands" width="600" height="361" viewBox="0 0 600 361" aria-hidden="true">
      <defs>
        <linearGradient id="bandDark" x1="0" x2="1" y1="0" y2="0">
          <stop offset="0" stop-color="var(--band-dark-start)"/>
          <stop offset="1" stop-color="var(--band-dark-end)"/>
        </linearGradient>
        <linearGradient id="bandLight" x1="0" x2="1" y1="0" y2="0">
          <stop offset="0" stop-color="var(--band-light-start)"/>
          <stop offset="1" stop-color="var(--band-light-end)"/>
        </linearGradient>
      </defs>
      <polygon points="334,265 600,265 600,316 309,316" fill="url(#bandDark)"/>
      <polygon points="0,316 309,316 286,361 0,361" fill="url(#bandLight)"/>
    </svg>

    <div class="person">
      <div class="person-name">Marlo Ashcombe</div>
      <div class="person-role">CEO &amp; Founder</div>
    </div>

    <div class="contact contact-phone">
      <svg width="16" height="14" viewBox="0 0 16 14" aria-hidden="true">
        <path d="M1 4 Q8 -1 15 4 L13 6 L11 4.5 L5 4.5 L3 6 Z" fill="var(--sky)"/>
        <rect x="3" y="6" width="10" height="7" rx="1" fill="var(--sky)"/>
      </svg>
      <span>555-201-4478</span>
    </div>
    <div class="contact contact-email">
      <svg width="12" height="9" viewBox="0 0 12 9" aria-hidden="true">
        <rect width="12" height="9" rx="1" fill="var(--band-dark-start)"/>
        <path d="M0.5 1 L6 5 L11.5 1" stroke="#fff" stroke-width="1" fill="none"/>
      </svg>
      <span>info@larkwellhealthpartners.com</span>
    </div>
    <div class="contact contact-web">
      <svg width="12" height="12" viewBox="0 0 12 12" aria-hidden="true">
        <circle cx="6" cy="6" r="5.5" fill="var(--sky)"/>
        <path d="M0.5 6 H11.5 M6 0.5 Q2.5 6 6 11.5 M6 0.5 Q9.5 6 6 11.5" stroke="#fff" stroke-width=".8" fill="none"/>
      </svg>
      <span>www.larkwellhealthpartners.com</span>
    </div>
  </section>

  <section class="card card-back" aria-label="Business card back">
    <span class="brand-dot"></span>
    <span class="brand-name">Larkwell Health Partners</span>
  </section>

</main>
</body>
</html>
```